Law Firm Profile

I need a Law firm Profile design. Something professional, corporate inspired, unique and sophisticated. Preferred colours are blue, grey and white. Completion timeline is 5 days. Details of law firm are in the uploaded document

```html
<!DOCTYPE html>
<html lang="en">
<head>
<meta charset="utf-8">
<title>KNB Advocates Law Firm – Tri-fold Profile</title>
<link href="https://fonts.googleapis.com/css2?family=Montserrat:wght@300;400;500;600&family=Oswald:wght@600&display=swap" rel="stylesheet">
<style>
:root{
  --blue:#1b70bd;
  --blue-deep:#1460a8;
  --grey:#6d6e71;
  --ink:#58595b;
  --white:#ffffff;
  --page:#eeeff0;
}
*{box-sizing:border-box;margin:0;padding:0}
html,body{width:1200px;height:2573px;overflow:hidden}
body{background:var(--page);font-family:"Montserrat",sans-serif;color:var(--ink);position:relative}
.spread{position:absolute;left:110px;width:980px;height:690px;display:flex;box-shadow:0 22px 30px -12px rgba(0,0,0,.35)}
.spread--outside{top:560px}
.spread--inside{top:1345px}
.panel{position:relative;width:327px;height:690px;overflow:hidden}
.panel--white{background:var(--white)}
.panel--blue{background:var(--blue);color:var(--white)}
.panel--fold{background:linear-gradient(90deg,#d9dadb 0%,#fff 12%,#fff 88%,#d9dadb 100%)}
.block{position:absolute;left:28px;right:28px}
h3.section{font-weight:500;font-size:13.5px;color:var(--blue);margin-bottom:3px}
.panel--blue h3.section{color:var(--white)}
p.copy{font-weight:300;font-size:10.4px;line-height:12.6px;text-align:justify}
.centered{text-align:center}
.heading-caps{font-weight:500;font-size:14px;color:var(--blue);letter-spacing:.3px;line-height:17px}
.photo{position:absolute;display:block}
.mark{position:absolute;display:flex;align-items:center;gap:8px;font-weight:500;font-size:13px;color:var(--blue)}
.mark__dot{width:14px;height:14px;border-radius:50%;background:var(--blue)}
.cover-badge{position:absolute;left:100px;top:315px;width:130px;height:130px;border-radius:50%;background:var(--blue);display:flex;align-items:center;justify-content:center;color:var(--white);font-weight:500;font-size:14px;text-align:center;line-height:17px}
.cover-title{position:absolute;left:0;right:0;top:455px;text-align:center;font-family:"Oswald",sans-serif;font-weight:600;font-size:62px;line-height:55px;color:var(--blue);letter-spacing:-.5px}
.cover-title .grey{color:var(--grey)}
.cover-url{position:absolute;left:0;right:0;top:655px;text-align:center;font-weight:500;font-size:13.5px;color:var(--grey);letter-spacing:.3px}
.rule-box{position:absolute;left:35px;right:35px;top:322px;height:118px;border-top:2px solid var(--blue);border-bottom:2px solid var(--blue);padding:7px 10px}
.contact{position:absolute;left:20px;right:20px;text-align:center;font-weight:300;font-size:11.2px;line-height:14px}
.email{font-weight:500;font-size:9.6px;color:var(--blue);letter-spacing:1px}
.staff-list{position:absolute;left:28px;top:548px;font-weight:400;font-size:10.4px;line-height:12.4px;list-style:none}
.staff-list b{font-weight:600}
.person{font-weight:500;font-size:13.5px;color:var(--blue);line-height:17px}
</style>
</head>
<body>

<!-- OUTSIDE SPREAD -->
<section class="spread spread--outside">

  <div class="panel panel--white">
    <div class="block" style="top:28px">
      <h3 class="section">Corporate Law</h3>
      <p class="copy">We provide comprehensive legal services for corporate clients including in the areas of corporate governance, regulatory compliance, due diligence and risk management advisory. We seamlessly manage the legal aspects of our clients’ transactions and ensure that all documentary and contractual requirements are professionally and strategically executed</p>
    </div>
    <div class="block" style="top:172px">
      <h3 class="section">Commercial Law</h3>
      <p class="copy">We have vast knowledge and experience in navigating complex commercial legal matters, including contract drafting, negotiations and compliance. We are aligned with the international environment and our lawyers keep up to date on evolving rules of international law and any applicable conflict of laws issues. Our lawyers understand the interplay between the evolving digitalization of the business environment, jurisdictional variances and the legal implications of innovations to the legal environment</p>
    </div>
    <svg class="photo" style="left:0;top:360px" width="327" height="330" viewBox="0 0 327 330" role="img" aria-label="Photo of a lawyer in a suit writing notes at a desk">
      <defs>
        <linearGradient id="deskTone" x1="0" y1="0" x2="1" y2="1">
          <stop offset="0" stop-color="#3b3a36"/>
          <stop offset=".55" stop-color="#8a7660"/>
          <stop offset="1" stop-color="#c9b48f"/>
        </linearGradient>
      </defs>
      <path d="M0 0 H180 A250 250 0 0 1 327 120 V330 H0 Z" fill="url(#deskTone)"/>
      <circle cx="330" cy="310" r="140" fill="var(--blue)"/>
    </svg>
  </div>

  <div class="panel panel--fold">
    <div class="mark" style="left:110px;top:48px"><span class="mark__dot"></span>KNB Advocates</div>
    <div class="block centered" style="top:125px">
      <div class="heading-caps" style="font-size:16px">CORE VALUES</div>
      <p class="copy" style="margin-top:7px">We take pride in the quality of our legal services in which we incorporate our core values which include integrity, passion, credibility, continuous professional development and excellent client care in the management of our clients’ instructions. The firm is regulated by the Zambia Legal Practitioners Council, and adherence to legal ethics and conduct forms the backbone of our practice and the firm’s culture. We also aim to efficiently to harness creative, bespoke and expert solutions to meet every client’s particular needs.</p>
    </div>
    <div class="rule-box">
      <p class="copy" style="text-align:justify;text-align-last:center">KNB Advocates is an established legal firm situated in Lusaka, Zambia. The firm was founded in 2013 by Mr Daniel K Mbewe S. C, the current Director of Public Prosecutions. The firm represents a wide range of clients both local and international and is dedicated to providing the highest quality of services in various areas of the law including</p>
    </div>
    <div class="contact" style="top:487px">
      <div class="heading-caps">BUSINESS ADDRESS<br>AND CONTACT INFORMATION</div>
      <div style="margin-top:8px">Plot No. 14, Kasempa Road,<br>Northmead Park</div>
      <div style="margin-top:7px">P.O. Box 41720, Longacres,<br>Lusaka, Zambia</div>
      <div class="heading-caps" style="margin-top:8px;letter-spacing:1.5px">CELL</div>
      <div>+260700412233 +260900518804<br>+260970336127 +260760229845</div>
      <div class="email" style="margin-top:12px">knbadvocates1@mailbox.net</div>
    </div>
  </div>

  <div class="panel panel--white">
    <svg class="photo" style="left:0;top:0" width="327" height="420" viewBox="0 0 327 420" role="img" aria-label="Photo of brass scales of justice, an open book and a wooden gavel">
      <defs>
        <linearGradient id="scalesTone" x1="0" y1="0" x2="1" y2="1">
          <stop offset="0" stop-color="#e9e4d8"/>
          <stop offset=".5" stop-color="#b99a6c"/>
          <stop offset="1" stop-color="#5d3a22"/>
        </linearGradient>
      </defs>
      <path d="M0 0 H327 V420 H0 Z" fill="url(#scalesTone)"/>
      <path d="M0 225 Q40 420 260 420 H0 Z" fill="#ffffff"/>
      <path d="M0 0 H210 A215 215 0 0 1 0 235 Z" fill="var(--blue)"/>
    </svg>
    <div class="cover-badge">KNB<br>Advocates</div>
    <h1 class="cover-title">KNB<br>ADVOCATES<br><span class="grey">LAW FIRM</span></h1>
    <div class="cover-url">www.knblawfirm.net</div>
  </div>
</section>

<!-- INSIDE SPREAD -->
<section class="spread spread--inside">

  <div class="panel panel--blue">
    <div class="block" style="top:33px">
      <h3 class="section">Estate and Family Law</h3>
      <p class="copy">We are well versed in handling estate planning, Wills, Trusts, guardianship, divorce and probate matters to address clients’ specific legal needs. Our flexible approach in implementing the full range of established dispute resolution methods at appropriate stages of the transactions and matters speaks to the successful management of even the most complex cases</p>
    </div>
    <svg class="photo" style="left:28px;top:152px" width="271" height="178" role="img" aria-label="Silhouette photo of a family holding up a paper house at sunset">
      <defs>
        <linearGradient id="sunsetTone" x1="0" y1="0" x2="0" y2="1">
          <stop offset="0" stop-color="#8c8f93"/>
          <stop offset=".6" stop-color="#c8a37a"/>
          <stop offset="1" stop-color="#2e2a26"/>
        </linearGradient>
      </defs>
      <rect width="271" height="178" fill="url(#sunsetTone)"/>
    </svg>
    <div class="block" style="top:342px">
      <h3 class="section">Debt Collection</h3>
      <p class="copy">We efficiently handle the recovery process which is crucial for the businesses, financial institutions and individuals we represent, ensuring that disruptions and cost to our clients are mitigated</p>
    </div>
    <div class="block" style="top:425px">
      <h3 class="section">Civil and Criminal Litigation</h3>
      <p class="copy">We have a notable and well respected track record in the area of litigation and all ancillary processes, we have handled major cases in commercial, criminal, constitutional and other areas of the law. We are committed to ensuring that our work is backed by meticulous legal analysis, structure and sound strategy, ensuring that we draw from the benefits of the integrated and multi-faceted nature of our practice to ensure best results for our clients</p>
    </div>
    <svg class="photo" style="left:28px;top:565px" width="271" height="107" role="img" aria-label="Photo of a judge's gavel beside a folded flag">
      <defs>
        <linearGradient id="gavelTone" x1="0" y1="0" x2="1" y2="0">
          <stop offset="0" stop-color="#4a4f5a"/>
          <stop offset=".5" stop-color="#2b2622"/>
          <stop offset="1" stop-color="#5a4a3e"/>
        </linearGradient>
      </defs>
      <rect width="271" height="107" fill="url(#gavelTone)"/>
    </svg>
  </div>

  <div class="panel panel--white">
    <div class="block" style="top:33px">
      <h3 class="section">Administrative Law</h3>
      <p class="copy">We represent a significant number of clients in the area of public law and have handled a large number of judicial review matters regarding immigration and deportation matters, regulatory infringements among others. We are committed to offering comprehensive guidance, clear communication and swift and appropriate response and high quality strategy from the administrative stage, at first instance, and across all stages of the appeal process</p>
    </div>
    <div class="block" style="top:173px">
      <h3 class="section">Land Law</h3>
      <p class="copy">We have handled a wide range of land matters including trespass litigation, encroachment, rectifications and conveyancing and manage a substantial caseload of cases</p>
    </div>
    <svg class="photo" style="left:28px;top:252px" width="271" height="108" role="img" aria-label="Aerial photo of green farmland plots with a marked parcel">
      <defs>
        <linearGradient id="landTone" x1="0" y1="0" x2="1" y2="1">
          <stop offset="0" stop-color="#6f9a3c"/>
          <stop offset=".6" stop-color="#3f6b2a"/>
          <stop offset="1" stop-color="#b2774c"/>
        </linearGradient>
      </defs>
      <rect width="271" height="108" fill="url(#landTone)"/>
    </svg>
    <div class="block" style="top:370px">
      <h3 class="section">Constitutional Law</h3>
      <p class="copy">We are a leading firm in constitutional law matters and have handled a plethora of presidential, parliamentary and local government election petitions. Our vast expertise in constitutional law is also displayed by our extensive portfolio in handling all manner of novel challenging matters in this area from constitutional interpretation to general constitutional petitions as well as motions. We have a strong database of case-law records and material which enhances our nuanced and detailed understanding of constitutional law enabling us to render well researched legal opinions to our clients</p>
    </div>
    <div class="block" style="top:545px">
      <div class="person">KEY PERSONNEL<br>MANAGING PARTNER<br>Grace Tembo</div>
      <p class="copy" style="margin-top:6px">Grace Tembo has more than seven years of experience in various areas of the law including commercial law, mining law, construction law, labour law, company law, constitutional law, human rights law, ICT law, administrative law, legislative drafting, civil and criminal litigation and energy law</p>
    </div>
  </div>

  <div class="panel panel--blue">
    <div class="block" style="top:33px">
      <p class="copy">studied law at the Kafue Valley University, graduated in 2015 and was admitted to the bar in 2016. Since April 2022She has sat on the licensing committee of the Power Sector Licensing Board and is well versed in the matters relating to the energy sector. She is a member of the Press Freedom Network and advocates for digital rights and freedom of expression. She provides legal advisory services to various civil society organizations and undertakes strategic litigation and she holds a postgraduate diploma in legislative drafting and advocates for legislative reform and advancement in various areas of the law</p>
    </div>
    <div class="block" style="top:194px">
      <h3 class="section">ASSOCIATE – Ruth Banda</h3>
      <p class="copy">Ruth Banda has over three years of experience in civil litigation, conveyancing, handling corporate and commercial transactions, contract drafting, family law, human rights law , labour disputes, debt recovery as well as administrative law. She studied at Northbank Open University and graduated in 2016 and was admitted to the Bar in 2020. She is a member of the Public Interest Committee of the Zambia Legal Practitioners Council and has a keen interest in human rights matters</p>
    </div>
    <div class="block" style="top:350px">
      <h3 class="section">Management Structure</h3>
      <p class="copy">We have a dedicated team of personnel whose primary goal is to provide the highest quality of service in compliance with all applicable rules of professional conduct. Our support team is friendly, skilled and diverse and work together to ensure that the lawyer-client relationship is seamlessly and properly managed</p>
    </div>
    <div class="mark" style="left:28px;top:495px;color:var(--white)"><span class="mark__dot" style="background:var(--white)"></span>KNB Advocates</div>
    <svg class="photo" style="left:175px;top:455px" width="152" height="200" role="img" aria-label="Photo of hands signing a document on a clipboard">
      <defs>
        <linearGradient id="signTone" x1="0" y1="0" x2="1" y2="1">
          <stop offset="0" stop-color="#d8cbbb"/>
          <stop offset=".6" stop-color="#9b7a62"/>
          <stop offset="1" stop-color="#4a3a30"/>
        </linearGradient>
      </defs>
      <circle cx="100" cy="100" r="100" fill="url(#signTone)"/>
    </svg>
    <ol class="staff-list">
      <li><b>1.</b> MANAGING PARTNER</li>
      <li><b>2.</b> PARTNER (S)</li>
      <li><b>3.</b> ASSOCIATE (S)</li>
      <li style="margin-top:4px"><b>SUPPORT STAFF:</b></li>
      <li><b>4.</b> OFFICE MANAGER</li>
      <li><b>5.</b> ASSISTANT OFFICE<br>&nbsp;&nbsp;&nbsp;&nbsp;MANAGER</li>
      <li><b>6.</b> LEGAL CLERK</li>
      <li><b>7.</b> RECEPTIONIST</li>
    </ol>
  </div>
</section>

</body>
</html>
```